Creating a website for a life changing company (Halvra Q)

We do need a website for our Coaching and Consulting business we recently launched. We do need it for information purposes and that our clients do have the opportunity to subscribe for packages, programs etc.
We would like to see designs which use the colours blue and yellow (see attachment). The final design should communicate our passion for the potential in people and the benefit (rising onward) for them.
Updates
Additional information:
Our company (webpage): Halvra Q (the C stands for "what people cannot see / imagine now...)
Welcome to Halvra Q(uarry)
Consulting (O.R.T.) & Coaching (Rise onward)
Two pillars:
1) O.R.T. ( Steward pathway - Our program - focussing on companies - business orientated)
2) Rise onward (Daily renewal - Events - focusing on individuals - primarily life changing)
For both of them we offer: Lanternhall & Halvra Q+ (This should go as a subscription)
Eventually you can draft this as a rhombus
Industry/Entity Type
Coaching / Consulting
Coding
Coded - Design and coding required
Number of Pages Required
1 page
Font styles to use
Other font styles liked:
- Lato
Requirements
Must have
- Please see attachment (About us / Offers / Calendar function / Links to Snapfold and Linkora account / mailing list / page for clients
Nice to have
- A banner

```html
<!DOCTYPE html>
<html lang="en">
<head>
<meta charset="utf-8">
<title>Halvra Q — Coaching &amp; Consulting</title>
<link rel="stylesheet" href="https://fonts.googleapis.com/css2?family=Lato:wght@400;700;900&display=swap">
<style>
:root{
  --navy:#0b3556;
  --blue:#1b69a6;
  --yellow:#ffd93b;
  --button:#fff200;
  --pale:#e7eef7;
  --text:#555;
  --white:#fff;
}
*{box-sizing:border-box;margin:0;padding:0}
html,body{width:1200px;height:3526px;overflow:hidden}
body{font-family:'Lato',sans-serif;color:var(--navy);background:var(--white);position:relative}
.abs{position:absolute}
.nav{display:flex;gap:0;justify-content:space-between;width:675px;left:380px;font-size:13px;font-weight:700;text-transform:uppercase}
.nav a{color:inherit;text-decoration:none}
.header{top:0;left:0;width:1200px;height:96px;background:var(--white)}
.header .nav{top:40px;color:#222}
.header .nav a.active{border-bottom:3px solid var(--yellow);padding-bottom:6px}
.brand{left:145px;top:34px;font-size:18px;font-weight:900;letter-spacing:4px;color:var(--navy)}
.brand::before{content:"";display:inline-block;width:14px;height:14px;border-radius:50%;background:var(--yellow);margin-right:8px;vertical-align:-1px}
.hero{top:96px;left:0;width:1200px;height:444px;background:var(--navy)}
.photo{border-radius:22px}
.hero-photo{left:144px;top:52px;width:590px;height:340px;background:linear-gradient(120deg,#c9a44a,#5a6a7a 50%,#24394f)}
.hero-title{left:798px;top:92px;font-size:52px;font-weight:900;color:var(--white);letter-spacing:-1px}
.hero-title span{color:var(--yellow)}
.hero-tag{left:798px;top:170px;font-size:19px;font-weight:700;color:var(--white)}
.hero-lede{left:798px;top:210px;font-size:18px;font-weight:700;color:var(--white);line-height:26px}
.btn{display:flex;align-items:center;justify-content:center;background:var(--button);color:var(--navy);font-weight:700;border-radius:30px;text-transform:uppercase}
.hero-btn{left:798px;top:291px;width:256px;height:51px;font-size:16px}
.dot{width:9px;height:9px;border-radius:50%;background:var(--white);left:1133px}
.h2{font-size:68px;font-weight:900;letter-spacing:-1px}
.h2 span{color:var(--yellow)}
.rule{height:4px;background:var(--yellow)}
.body-text{font-size:14.5px;line-height:24px;color:var(--text);text-align:justify}
.about-title{left:145px;top:603px}
.about-intro{left:581px;top:612px;width:474px}
.person-photo{top:776px;width:411px;height:357px}
.person-name{top:1176px;width:411px;text-align:center;font-size:24px;font-weight:900}
.person-text{top:1230px;width:405px;text-align:justify;text-align-last:center}
.more-btn{top:1479px;width:151px;height:51px;font-size:17px}
.programs{top:1607px;left:0;width:1200px;height:593px;background:var(--pale)}
.programs-title{top:76px;width:1200px;text-align:center}
.programs-lede{top:198px;width:1200px;text-align:center;font-size:19px;color:#222}
.card{top:266px;width:284px;height:237px}
.card .art{height:185px}
.card .label{height:52px;display:flex;align-items:center;justify-content:center;font-size:23px;font-weight:900}
.events-photo{top:2200px;left:0;width:594px;height:312px;background:linear-gradient(180deg,#3d4631,#6d5a2d 60%,#b5872b)}
.events-title{top:2410px;left:0;width:594px;text-align:center;font-size:64px;font-weight:900;color:var(--white)}
.events-band{top:2512px;left:0;width:594px;height:133px;background:var(--blue);color:var(--white);text-align:center}
.events-band h3{margin-top:26px;font-size:21px;font-weight:900;color:var(--yellow);text-align:left;padding-left:145px}
.events-band p{margin-top:16px;font-size:13px;line-height:20px}
.calendar{top:2200px;left:594px;width:606px;height:445px;background:var(--white)}
.cal-head{left:117px;top:0;width:371px;height:50px;background:var(--blue);color:var(--white);font-size:24px;font-weight:900;display:flex;align-items:center;justify-content:center}
.cal-arrow{top:9px;width:32px;height:32px;border-radius:50%;background:var(--white)}
.cal-grid{left:45px;top:104px;width:530px;display:grid;grid-template-columns:repeat(7,1fr);row-gap:25px;text-align:center;font-size:18px;color:#333}
.cal-grid .dow{font-weight:700;font-size:17px;margin-bottom:8px}
.cal-grid .off{color:#ccc}
.cal-grid .today{justify-self:center;width:38px;height:38px;margin-top:-9px;border-radius:50%;background:var(--button);color:var(--blue);line-height:38px}
.contact-photo{left:146px;top:2744px;width:399px;height:417px;background:linear-gradient(135deg,#2b3f4f,#6f5b3e 60%,#9a7a4d)}
.contact-title{left:624px;top:2728px}
.field{border:1.5px solid #bbb;height:51px;font-size:15px;color:#333;padding:18px 0 0 28px}
.submit{left:624px;top:3112px;width:152px;height:52px;font-size:17px}
.footer{top:3248px;left:0;width:1200px;height:278px;background:var(--navy);color:var(--white)}
.footer .nav{top:67px;color:var(--white)}
.footer-brand{left:145px;top:128px;font-size:28px;font-weight:700;letter-spacing:8px}
.social{width:41px;height:41px;border:2px solid var(--white);border-radius:50%;top:128px}
.sub-label{left:535px;top:138px;font-size:17px;font-weight:900}
.sub-form{left:800px;top:128px;width:255px;height:41px;background:var(--white);border-radius:22px;overflow:hidden}
.sub-form .email{left:30px;top:13px;font-size:12px;color:#333}
.sub-form .go{right:0;top:0;width:118px;height:41px;font-size:14px;border-radius:22px}
.copy{left:380px;top:208px;font-size:12px}
</style>
</head>
<body>

<header class="header abs">
  <div class="brand abs">HALVRA Q</div>
  <nav class="nav abs">
    <a class="active">Halvra Q</a><a>About Us</a><a>O.R.T.</a><a>Lanternhall</a><a>Rise Onward</a><a>Halvra Q+</a><a>Testimonials</a>
  </nav>
</header>

<section class="hero abs">
  <div class="hero-photo photo abs" role="img" aria-label="Two consultants smiling across a table with a laptop"></div>
  <h1 class="hero-title abs">HALVRA <span>Q</span></h1>
  <p class="hero-tag abs">WE O.R.T. YOUR COMPANY</p>
  <p class="hero-lede abs">We ignite the Passion in People<br>to unleash their full Potential!</p>
  <a class="hero-btn btn abs">Subscribe for programs</a>
  <span class="dot abs" style="top:190px"></span>
  <span class="dot abs" style="top:218px;background:var(--yellow)"></span>
  <span class="dot abs" style="top:245px"></span>
</section>

<section class="about">
  <h2 class="about-title h2 abs">About <span>Us</span></h2>
  <div class="rule abs" style="left:145px;top:693px;width:90px"></div>
  <p class="about-intro body-text abs">Where Passion for igniting People's Potential is in our DNA and brought Us together. The journey starts in the Himalayas to Everest Base Camp, where transformation happened for both of them, it was rising onward (Q) what they could see, comprehend and imagine.</p>

  <div class="person-photo photo abs" style="left:144px;background:linear-gradient(160deg,#4a4a42,#2c4c78 55%,#1c2f4f)" role="img" aria-label="Portrait of Marek in a blue suit"></div>
  <h3 class="person-name abs" style="left:144px">ABOUT MAREK</h3>
  <p class="person-text body-text abs" style="left:147px">I could tell you all about my facilitation and coaching experience. my degrees, and certificates. But none of that would tell you much about what matters most in working with me: the passion and support you will experience, the trust, the honesty, and the sense of growth and ease. The essence of my work is to facilitate self-growth by helping people identify the core challenges and setbacks in their lives so that they can overcome them with confidence. I call it "Living a passionate and cherish life</p>
  <a class="more-btn btn abs" style="left:273px">Read more</a>

  <div class="person-photo photo abs" style="left:644px;background:linear-gradient(150deg,#2fa8b0,#3f5a3a 55%,#8c8a6a)" role="img" aria-label="Portrait of Liesel holding a teal umbrella outdoors"></div>
  <h3 class="person-name abs" style="left:644px">ABOUT LIESEL</h3>
  <p class="person-text body-text abs" style="left:647px">In my twenty years of work experience, people were always at the centre of everything I did, honouring everyone's uniqueness and preferences. Understanding a person's ambitions gives me insights into the type of support, experiences, partnerships, and nurturing they need to thrive. My strength is to find insight into how each human being is unique and distinct from everyone else and open people's minds to new and wondrous possibilities. I take pride in looking for ways to improve</p>
  <a class="more-btn btn abs" style="left:774px">Read more</a>
</section>

<section class="programs abs">
  <h2 class="programs-title h2 abs">Lanternhall <span>Programs</span></h2>
  <div class="rule abs" style="left:554px;top:166px;width:92px"></div>
  <p class="programs-lede abs">Lanternhall Package offers you an ongoing partnership as you navigate your journey to reach your full potential.</p>
  <div class="card abs" style="left:144px">
    <div class="art" style="background:linear-gradient(135deg,#f2f2f2,#d8d8d8)" role="img" aria-label="Word cloud about coaching"></div>
    <div class="label" style="background:var(--button);color:var(--navy)">COACHING</div>
  </div>
  <div class="card abs" style="left:458px">
    <div class="art" style="background:linear-gradient(135deg,#e6e6e6,#9a9a9a)" role="img" aria-label="Sketch of a strategy and consulting process on a wall"></div>
    <div class="label" style="background:var(--blue);color:var(--white)">CONSULTING</div>
  </div>
  <div class="card abs" style="left:772px">
    <div class="art" style="background:radial-gradient(circle at 45% 40%,#f4f4f4 0 30%,#4a4d52 32%)" role="img" aria-label="White speech bubble on a dark slate"></div>
    <div class="label" style="background:var(--button);color:var(--navy)">FIRESIDE CHAT</div>
  </div>
</section>

<section class="events">
  <div class="events-photo abs" role="img" aria-label="Hiker with a backpack in a mountain forest"></div>
  <h2 class="events-title abs">Rise Onward</h2>
  <div class="events-band abs">
    <h3>RISE ONWARD LIGHT (HALF DAY)</h3>
    <p>This is a fantastic opportunity to understand, WHY you<br>carry the heavy backpack throughout your life.</p>
  </div>

  <div class="calendar abs">
    <div class="cal-head abs">
      <span class="cal-arrow abs" style="left:18px"><svg width="32" height="32" viewBox="0 0 32 32"><path d="M23 16H9M14 11l-5 5 5 5" stroke="#1b69a6" stroke-width="2.2" fill="none"/></svg></span>
      SEPTEMBER 2022
      <span class="cal-arrow abs" style="right:18px"><svg width="32" height="32" viewBox="0 0 32 32"><path d="M9 16h14M18 11l5 5-5 5" stroke="#1b69a6" stroke-width="2.2" fill="none"/></svg></span>
    </div>
    <div class="cal-grid abs">
      <span class="dow">MO</span><span class="dow">TUE</span><span class="dow">WED</span><span class="dow">THU</span><span class="dow">FRI</span><span class="dow">SAT</span><span class="dow">SUN</span>
      <span class="off">29</span><span class="off">30</span><span class="off">31</span><span>1</span><span>2</span><span>3</span><span>4</span>
      <span>5</span><span>6</span><span>7</span><span class="today">8</span><span>9</span><span>10</span><span>11</span>
      <span>12</span><span>13</span><span>14</span><span>15</span><span>16</span><span>17</span><span>18</span>
      <span>19</span><span>20</span><span>21</span><span>22</span><span>23</span><span>24</span><span>25</span>
      <span>26</span><span>27</span><span>28</span><span>29</span><span>30</span><span class="off">1</span><span class="off">2</span>
    </div>
  </div>
</section>

<section class="contact">
  <div class="contact-photo photo abs" role="img" aria-label="Coaching session at a restaurant table"></div>
  <h2 class="contact-title h2 abs">Contact <span>Us</span></h2>
  <div class="rule abs" style="left:624px;top:2818px;width:90px"></div>
  <div class="field abs" style="left:624px;top:2861px;width:210px">Enter Name</div>
  <div class="field abs" style="left:844px;top:2861px;width:211px">Enter Email</div>
  <div class="field abs" style="left:624px;top:2924px;width:210px">Phone</div>
  <div class="field abs" style="left:844px;top:2924px;width:211px">Address</div>
  <div class="field abs" style="left:624px;top:2988px;width:431px;height:98px">Message</div>
  <a class="submit btn abs">Submit</a>
</section>

<footer class="footer abs">
  <div class="footer-brand abs">HALVRA Q</div>
  <nav class="nav abs">
    <a>Halvra Q</a><a>About Us</a><a>O.R.T.</a><a>Lanternhall</a><a>Rise Onward</a><a>Halvra Q+</a><a>Testimonials</a>
  </nav>
  <span class="social abs" style="left:381px" role="img" aria-label="Linkora profile"></span>
  <span class="social abs" style="left:431px" role="img" aria-label="Snapfold profile"></span>
  <div class="sub-label abs">SUBSCRIBE FOR PACKAGES</div>
  <div class="sub-form abs">
    <span class="email abs">Enter Email</span>
    <a class="go btn abs">Subscribe</a>
  </div>
  <p class="copy abs">© 2022 Halvra Q.All rights reserved.Privacy &nbsp;|&nbsp; Terms of Use</p>
</footer>

</body>
</html>
```